Logo and Card design for KRV Home Solutions LLC

I need an edgier logo and business card designs. Current logo attached. I like the colors below. I would like the logo to incorporate a home in the design.
Title = Principal-Acquisitions
Email:KRVHOMESOLUTIONS@fernmail.example
555-214-0937
facebook
IG
2 sided business card with the front being contact info a slogan about selling a home fast. The back incorporating What we do. Buy houses, land, or commercial property as is. We find solutions to make the process of selling simple and fair.

Target Market(s)

Motivated house sellers.

Industry/Entity Type

Business

Contact Information for Business Card

Who we are: We are a Faith based Real Estate Investment Company. We pay cash for homes in any condition and can close quick. Whatever the reason you need to sell fast, we can help. We believe in creating win-win solutions to help you in your time of need. We care! We can help!

Logo Text

KRV Home Solutions LLC

Font styles to use
Sans Serif

Colors
33a6d7
0355a3
85abd2
cee9f5
9d9d9d
b2b2b2
ffffff

Requirements
Must have
• Old logo attached. I want something edgier.
• Company name, phone number, description on the back of what we can do. Pay all cash. Buy in as is condition. No fees,Commisions or closing costs.Close quick. No hassles with solutions to meet your unique situation.
• Call today for an offer within 24 hours.

```html
<!DOCTYPE html>
<html lang="en">
<head>
<meta charset="utf-8">
<title>KRV Home Solutions – Business Card</title>
<link rel="stylesheet" href="https://fonts.googleapis.com/css2?family=Roboto:wght@400;500;700&family=Roboto+Condensed:wght@400&display=swap">
<style>
  :root {
    --navy: #1f3566;
    --slate: #555a62;
    --ink: #3c4048;
    --white: #ffffff;
    --mist: #dfe6ec;
    --stage: #2a2a2a;
  }
  * { margin: 0; padding: 0; box-sizing: border-box; }
  html, body { width: 1200px; height: 960px; overflow: hidden; }
  body { background: var(--stage); font-family: "Roboto", Arial, sans-serif; position: relative; }

  .card {
    position: absolute;
    width: 600px;
    height: 343px;
    overflow: hidden;
    box-shadow: 0 2px 6px rgba(0,0,0,.45);
  }
  .card--front { left: 314px; top: 113px; background: var(--mist); }
  .card--back { left: 311px; top: 472px; background: var(--navy); color: var(--white); text-align: center; }

  .front__photo {
    position: absolute; left: 0; top: 0; width: 600px; height: 258px;
    background: linear-gradient(160deg, #eef2f5 0%, #dbe4ea 40%, #c9d6dd 70%, #b9cbd3 100%);
  }
  .front__rule { position: absolute; left: 0; top: 258px; width: 600px; height: 2px; background: #8f9aa8; }
  .front__band {
    position: absolute; left: 0; top: 261px; width: 600px; height: 82px;
    background: var(--navy);
    color: var(--white);
    font-family: "Roboto Condensed", "Arial Narrow", sans-serif;
    font-size: 14.5px; line-height: 18.5px;
    text-align: center;
    padding-top: 12px;
  }

  .brand-name { font-family: "Roboto", Arial, sans-serif; font-weight: 700; white-space: nowrap; }
  .brand-name--front {
    position: absolute; left: 38px; top: 102px;
    color: var(--navy); font-size: 19px; line-height: 24px;
  }
  .brand-name--back {
    position: absolute; left: 0; right: 0; top: 96px;
    color: var(--white); font-size: 26px; line-height: 32px;
  }

  .person { position: absolute; right: 44px; top: 46px; text-align: right; }
  .person__name { color: var(--navy); font-weight: 700; font-size: 22px; line-height: 24px; }
  .person__title { color: var(--slate); font-weight: 700; font-size: 15px; letter-spacing: .3px; margin-top: 1px; }

  .contacts { position: absolute; left: 38px; top: 182px; list-style: none; }
  .contacts li { display: flex; align-items: center; height: 19px; color: var(--ink); font-size: 14.5px; }
  .contacts svg { width: 13px; height: 13px; margin-right: 9px; fill: var(--navy); flex: none; }

  .section { position: absolute; left: 0; right: 0; }
  .section--who { top: 168px; }
  .section--what { top: 254px; }
  .section__head { font-weight: 700; font-size: 15px; line-height: 20px; }
  .section__body { font-size: 14.5px; line-height: 18px; margin: 0 44px; }
</style>
</head>
<body>
  <article class="card card--front">
    <div class="front__photo" role="img" aria-label="Soft, faded photograph of a two-storey house with trees"></div>

    <p class="brand-name brand-name--front">KRV Home Solutions LLC</p>

    <div class="person">
      <p class="person__name">JORDAN REYES</p>
      <p class="person__title">PRINCIPAL–ACQUISITIONS</p>
    </div>

    <ul class="contacts">
      <li><svg viewBox="0 0 24 24"><path d="M6.6 10.8a15 15 0 0 0 6.6 6.6l2.2-2.2c.3-.3.7-.4 1-.2 1.1.4 2.3.6 3.6.6.6 0 1 .4 1 1V20c0 .6-.4 1-1 1A17 17 0 0 1 3 4c0-.6.4-1 1-1h3.5c.6 0 1 .4 1 1 0 1.3.2 2.5.6 3.6.1.3 0 .7-.2 1z"/></svg>555-214-0937</li>
      <li><svg viewBox="0 0 24 24"><path d="M2 5h20v14H2z"/><path d="M2 5l10 8 10-8" fill="none" stroke="#dfe6ec" stroke-width="2"/></svg>KRVHOMESOLUTIONS@fernmail.example</li>
      <li><svg viewBox="0 0 24 24"><circle cx="12" cy="12" r="10"/><path d="M2 12h20M12 2c3 3 3 17 0 20M12 2c-3 3-3 17 0 20" fill="none" stroke="#dfe6ec" stroke-width="1.5"/></svg>KRVHOMESOLUTIONS.example</li>
    </ul>

    <div class="front__rule"></div>
    <div class="front__band">
      <p>Pay all cash. Buy in as is condition.• No fees,Commisions or closing costs.</p>
      <p>Close quick. No hassles with solutions to meet your unique situation.</p>
      <p>Call today for an offer within 24 hours.</p>
    </div>
  </article>

  <article class="card card--back">
    <p class="brand-name brand-name--back">KRV Home Solutions LLC</p>

    <section class="section section--who">
      <h2 class="section__head">WHO WE ARE</h2>
      <p class="section__body">We are a Faith based Real Estate Investment Company. We pay cash for<br>homes in any condition and can close quick. Whatever the reason you need<br>to sell fast, we can help. We believe in creating win-win solutions to help</p>
    </section>

    <section class="section section--what">
      <h2 class="section__head">WHAT WE DO</h2>
      <p class="section__body">Buy houses, land, or commercial property as is.<br>We find solutions to make the process of selling simple and fair.</p>
    </section>
  </article>
</body>
</html>
```